Business Card for Multi-Brand Sportswear Company

We are looking for a business card which represents our company and the multiple brands within it.

The company: Fen Athletics (LTD)
The brands: Fen, TavaPuni, ElmStretch, Grit and Rain

Employees using these cards would be representing Fen Athletics, rather than any of the individual brands. You will see a current design within the uploaded files, to give some inspiration. The actual text of the brands is not necessary, but the logos should be on there is some format.

Our creative minds on this are stretched, so we are looking for someone to make this their own, and show us what a good business card should look like.

We may like to get these printed with spot gloss, so keep that in mind with your designs.

www.fenathletics.co.uk

Industry/Entity Type

Business

Contact Information for Business Card

Leo Pemberton-Hale
Operations Manager
(+44) 1632 960 418
Leo@fenathletics.co.uk
www.fenathletics.co.uk

Font styles to use
Sans Serif
Other font styles liked:
• Eurostile

Colors
ffffff

Requirements
Nice to have
• Dark (black) background

```html
<!DOCTYPE html>
<html lang="en">
<head>
<meta charset="utf-8">
<title>Fen Athletics – Business Card</title>
<link rel="stylesheet" href="https://fonts.googleapis.com/css2?family=Oxanium:wght@400;700&display=swap">
<style>
  :root {
    --stage: #3a302b;
    --card: #141414;
    --card-edge: #1d1d1d;
    --red: #e0251f;
    --white: #ffffff;
    --muted: #cfcfcf;
    --gloss: #2b2b2b;
    --purple: #6b4f8a;
    --grey-mark: #8a8a8a;
  }
  * { margin: 0; padding: 0; box-sizing: border-box; }
  html, body { width: 1200px; height: 716px; overflow: hidden; }
  body {
    background: var(--stage);
    font-family: "Oxanium", sans-serif;
    color: var(--white);
    position: relative;
  }
  .card {
    position: absolute;
    top: 203px;
    width: 540px;
    height: 310px;
    background: var(--card);
    border: 1px solid var(--card-edge);
    border-radius: 4px;
    overflow: hidden;
  }
  .card--back { left: 40px; }
  .card--front { left: 620px; }

  /* Back: spot-gloss wordmark */
  .gloss-mark {
    position: absolute;
    inset: 0;
    display: flex;
    align-items: center;
    justify-content: center;
    font-size: 34px;
    font-weight: 700;
    letter-spacing: 3px;
    color: var(--gloss);
  }

  /* Front */
  .band { position: absolute; left: 0; top: 0; }
  .band-mark {
    position: absolute;
    right: 22px;
    top: 58px;
    font-size: 21px;
    font-weight: 700;
    letter-spacing: 1px;
    color: var(--card);
  }
  .holder { position: absolute; left: 28px; top: 100px; }
  .holder-name { font-size: 17px; font-weight: 400; }
  .holder-name strong { font-weight: 700; }
  .holder-role { font-size: 12px; color: var(--muted); margin-top: 3px; }
  .address {
    position: absolute; left: 28px; top: 150px;
    font-size: 11.5px; line-height: 17px; color: var(--muted);
  }
  .contacts { position: absolute; left: 230px; top: 140px; list-style: none; }
  .contact {
    display: flex; align-items: center; height: 36px;
    font-size: 15px;
  }
  .contact svg { margin-right: 12px; flex: none; }
  .brands {
    position: absolute; left: 28px; right: 28px; bottom: 22px;
    display: flex; justify-content: space-between; align-items: center;
    list-style: none;
    font-size: 11px; font-weight: 700;
  }
  .brand { display: flex; align-items: center; gap: 5px; }
  .brand-dot { width: 10px; height: 10px; flex: none; }
  .brand--tava .brand-dot { background: var(--purple); }
  .brand--grit { color: var(--red); }
  .brand--grit .brand-dot { border: 1.5px solid var(--red); border-radius: 50%; }
  .brand--elm { color: var(--grey-mark); }
  .brand--elm .brand-dot { border: 1.5px solid var(--grey-mark); border-radius: 50%; }
</style>
</head>
<body>

<section class="card card--back" aria-label="Card reverse">
  <div class="gloss-mark">FEN ATHLETICS</div>
</section>

<section class="card card--front" aria-label="Card front">
  <svg class="band" width="540" height="110" viewBox="0 0 540 110" aria-hidden="true">
    <polygon points="10,16 40,16 28,48 -2,48" fill="var(--red)"/>
    <polygon points="50,16 80,16 68,48 38,48" fill="var(--red)"/>
    <polygon points="90,16 120,16 108,48 78,48" fill="var(--red)"/>
    <polygon points="130,16 160,16 148,48 118,48" fill="var(--red)"/>
    <polygon points="172,16 540,16 540,100 270,100 236,48 160,48" fill="var(--red)"/>
  </svg>
  <div class="band-mark">FEN ATHLETICS</div>

  <div class="holder">
    <p class="holder-name"><strong>Leo</strong> Pemberton-Hale</p>
    <p class="holder-role">Operations Manager</p>
  </div>

  <address class="address" style="font-style:normal">
    Carr Field, Westby,<br>Northam, NM4 2QT
  </address>

  <ul class="contacts">
    <li class="contact">
      <svg width="56" height="26" viewBox="0 0 56 26" aria-hidden="true">
        <path d="M0 9 H30 M6 13 H30 M12 17 H30" stroke="var(--red)" stroke-width="2"/>
        <circle cx="43" cy="13" r="11" fill="var(--card)" stroke="var(--red)" stroke-width="2"/>
        <path d="M39 8 l2 -1 2 3 -1.5 1.5 q1 2.5 3 3.5 l1.5 -1.5 3 2 -1 2 q-5 0 -9 -9.5z" fill="var(--white)"/>
      </svg>
      +44 (0)1632 960418
    </li>
    <li class="contact">
      <svg width="56" height="26" viewBox="0 0 56 26" aria-hidden="true">
        <path d="M0 9 H30 M6 13 H30 M12 17 H30" stroke="var(--red)" stroke-width="2"/>
        <circle cx="43" cy="13" r="11" fill="var(--card)" stroke="var(--red)" stroke-width="2"/>
        <rect x="37" y="9" width="12" height="8" fill="none" stroke="var(--white)" stroke-width="1.4"/>
        <path d="M37 9 L43 14 L49 9" fill="none" stroke="var(--white)" stroke-width="1.4"/>
      </svg>
      leo@fenathletics.co.uk
    </li>
    <li class="contact">
      <svg width="56" height="26" viewBox="0 0 56 26" aria-hidden="true">
        <path d="M0 9 H30 M6 13 H30 M12 17 H30" stroke="var(--red)" stroke-width="2"/>
        <circle cx="43" cy="13" r="11" fill="var(--card)" stroke="var(--red)" stroke-width="2"/>
        <g fill="none" stroke="var(--white)" stroke-width="1.3">
          <circle cx="43" cy="13" r="6.5"/>
          <ellipse cx="43" cy="13" rx="3" ry="6.5"/>
          <path d="M36.5 13 H49.5"/>
        </g>
      </svg>
      www.fenathletics.co.uk
    </li>
  </ul>

  <ul class="brands" aria-label="Group brands">
    <li class="brand brand--tava"><span class="brand-dot"></span>TavaPuni</li>
    <li class="brand brand--grit"><span class="brand-dot"></span>Grit and Rain</li>
    <li class="brand brand--fen">Fen</li>
    <li class="brand brand--elm"><span class="brand-dot"></span>ElmStretch</li>
  </ul>
</section>

</body>
</html>
```